Lawn sign for construction company

Would like this to be a very clean and high end design for luxury homes. We need a yard sign designed that includes the company logo, website, phone number and major service offerings (residential and commercial renovations and maintenance)
The company website is brackwellbuilders.com all other contact info is in the attachments
Target Market(s)
Luxury home owners and business owners
Industry/Entity Type
Construction/Home Improvement
Font styles to use
Other font styles liked:
- See company logo and other graphics included for title text fonts. All other fonts can be standard sans serif.
Colors
0054AA
0677BA
7BADD7
CADEEF
E8F1F8
Requirements
Must have
- Clean, easy to read design, would like 2 sided sign. A main sign side and back side which states “free estimates, and includes the website and phone number. Must also match the color scheme of the provided logo and other company images. Dark Navy blue primary color, gray secondary color, and orange as an accent color.
Nice to have
- 2nd sign side very simple design
Should not have
- Too many graphics limit to 1-3 colors

```html
<!DOCTYPE html>
<html lang="en">
<head>
<meta charset="utf-8">
<title>Halden Construction Company – Yard Sign</title>
<link rel="stylesheet" href="https://fonts.googleapis.com/css2?family=Germania+One&family=Open+Sans:wght@700&display=swap">
<style>
  :root {
    --stage-dark: #d1d2d4;
    --stage-light: #e7e8ea;
    --label-ink: #3b3b3b;
    --navy: #101b37;
    --orange: #e57828;
    --white: #ffffff;
  }
  html, body {
    margin: 0;
    padding: 0;
    overflow: hidden;
  }
  .canvas {
    position: relative;
    width: 1200px;
    height: 490px;
    overflow: hidden;
    background: var(--stage-light);
  }
  .stage-band {
    position: absolute;
    inset: 0;
    width: 1200px;
    height: 490px;
  }
  .side-label {
    position: absolute;
    top: 34px;
    width: 476px;
    margin: 0;
    text-align: center;
    font-family: "Open Sans", sans-serif;
    font-weight: 700;
    font-size: 39px;
    line-height: 1;
    color: var(--label-ink);
  }
  .side-label--front { left: 105px; }
  .side-label--back { left: 632px; }

  .sign {
    position: absolute;
    top: 121px;
    width: 476px;
    height: 312px;
    overflow: hidden;
    background: var(--orange);
  }
  .sign--front { left: 103px; }
  .sign--back { left: 621px; }

  .sign__field {
    position: absolute;
    left: 30px;
    top: -44px;
    width: 416px;
    height: 400px;
    border-radius: 50%;
    background: var(--navy);
  }
  .brand-name {
    position: absolute;
    left: 0;
    width: 476px;
    margin: 0;
    text-align: center;
    font-family: "Germania One", serif;
    font-weight: 400;
    color: var(--orange);
    line-height: 1.05;
    letter-spacing: 0.5px;
  }
  .sign--front .brand-name { top: 82px; font-size: 30px; }
  .sign--back .brand-name { top: 84px; font-size: 27px; }

  .divider {
    position: absolute;
    left: 76px;
    top: 197px;
    width: 324px;
    height: 1.5px;
    background: var(--orange);
  }
  .sign-text {
    position: absolute;
    left: 0;
    width: 476px;
    margin: 0;
    text-align: center;
    font-family: "Germania One", serif;
    color: var(--white);
    line-height: 1;
    white-space: nowrap;
  }
  .headline { top: 203px; font-size: 40px; letter-spacing: 1px; }
  .sign--front .web { top: 242px; font-size: 29px; }
  .sign--front .phone { top: 270px; font-size: 28px; }
  .sign--back .phone { top: 201px; font-size: 32px; }
  .sign--back .web { top: 236px; font-size: 33px; }
</style>
</head>
<body>
<main class="canvas">
  <svg class="stage-band" viewBox="0 0 1200 490" aria-hidden="true">
    <polygon points="0,0 1200,0 0,489" fill="var(--stage-dark)"/>
  </svg>

  <h2 class="side-label side-label--front">Front</h2>
  <h2 class="side-label side-label--back">back</h2>

  <section class="sign sign--front" aria-label="Sign front">
    <div class="sign__field"></div>
    <p class="brand-name">HALDEN CONSTRUCTION<br>COMPANY</p>
    <div class="divider"></div>
    <p class="sign-text headline">FREE ESTIMATES</p>
    <p class="sign-text web">brackwellbuilders.com</p>
    <p class="sign-text phone">+1 (555) 014-2287</p>
  </section>

  <section class="sign sign--back" aria-label="Sign back">
    <div class="sign__field"></div>
    <p class="brand-name">HALDEN CONSTRUCTION<br>COMPANY</p>
    <p class="sign-text phone">+1 (555) 014-2287</p>
    <p class="sign-text web">brackwellbuilders.com</p>
  </section>
</main>
</body>
</html>
```